High Tech Real Estate Startup needs a business card

We are developing an innovative real estate marketing product based around advanced search and virtual reality.

We talk to people, we need business cards.

Target Market(s)

The target market is technology professionals and realtors.

Contact Information for Business Card

The information to be included will include

Name
Title
Phone Number
E-mail Address
www.zelquin.com

It should use simple iconography for each one of those fields.

Font styles to use
Other font styles liked:
• Co, Jubilat, Avenir

Colors

Designer to choose colors to be used in the design.

Requirements
Must have
• Clean aesthetic,
• Good use of negative space.
• It should use our company logo, shown in the attached file. It is able to use the negative of that logo (coloured font and white background) and I have attached other acceptable accent colours in a swatch file.
Should not have
• Should not be too busy
• No extraneous text (slogans, tag lines etc)

```html
<!DOCTYPE html>
<html lang="en">
<head>
<meta charset="utf-8">
<title>Zelquin Business Card</title>
<link href="https://fonts.googleapis.com/css2?family=Work+Sans:wght@400;500&display=swap" rel="stylesheet">
<style>
  :root {
    --backdrop: #2a2a2b;
    --card: #1c1c1d;
    --card-edge: #242425;
    --accent: #1bbcc4;
    --ink: #f2f2f2;
  }
  * { margin: 0; padding: 0; box-sizing: border-box; }
  html, body {
    width: 1200px; height: 900px; overflow: hidden;
    background: var(--backdrop);
    font-family: "Work Sans", Arial, sans-serif;
  }
  .canvas {
    width: 1200px; height: 900px;
    display: flex; flex-direction: column; align-items: center; justify-content: center;
    gap: 44px;
  }
  .card {
    position: relative;
    width: 630px; height: 360px;
    background: linear-gradient(135deg, var(--card) 0%, var(--card-edge) 100%);
    box-shadow: 0 10px 28px rgba(0,0,0,.45);
    overflow: hidden;
  }
  .card__band {
    position: absolute; left: 0; right: 0; bottom: 0;
    height: 6px; background: var(--accent);
  }
  .wordmark {
    color: var(--accent);
    font-weight: 500;
    letter-spacing: 3px;
    line-height: 1;
  }
  .card--front { display: flex; align-items: center; justify-content: center; }
  .card--front .wordmark { font-size: 72px; margin-top: -8px; }

  .card--back { display: flex; align-items: center; }
  .card--back .wordmark { font-size: 58px; margin-left: 54px; width: 280px; }
  .divider {
    width: 2px; height: 150px; background: var(--accent);
    margin: 0 34px 0 24px;
  }
  .contact { color: var(--ink); font-size: 15px; line-height: 1.35; }
  .contact__name {
    color: var(--accent); font-size: 20px; font-weight: 500;
    letter-spacing: 1px; text-transform: uppercase; line-height: 1.1;
  }
  .contact__title { font-size: 15px; margin-bottom: 12px; }
  .contact__address { margin-bottom: 4px; letter-spacing: .5px; }
  .contact__row { display: flex; align-items: center; gap: 10px; letter-spacing: .5px; }
  .contact__row svg { width: 11px; height: 11px; flex: none; }
</style>
</head>
<body>
<main class="canvas">
  <section class="card card--front">
    <div class="wordmark">ZELQUIN</div>
    <div class="card__band"></div>
  </section>

  <section class="card card--back">
    <div class="wordmark">ZELQUIN</div>
    <div class="divider"></div>
    <div class="contact">
      <div class="contact__name">Dorian Hale</div>
      <div class="contact__title">Director</div>
      <div class="contact__address">417 Alder Ridge Ln.<br>Franklin, TN 37064</div>
      <div class="contact__row">
        <svg viewBox="0 0 12 12" aria-hidden="true"><path d="M2.5 1l2 2.2-1 1.3c.6 1.4 1.6 2.4 3 3l1.3-1 2.2 2-1 1.5C5 10 2 7 1 2.5z" fill="var(--accent)"/></svg>
        <span>+1-615-555-0148</span>
      </div>
      <div class="contact__row">
        <svg viewBox="0 0 12 12" aria-hidden="true"><rect x="1" y="2.5" width="10" height="7" fill="none" stroke="var(--accent)" stroke-width="1.2"/><path d="M1 2.5l5 4 5-4" fill="none" stroke="var(--accent)" stroke-width="1.2"/></svg>
        <span>info@zelquin.com</span>
      </div>
      <div class="contact__row">
        <svg viewBox="0 0 12 12" aria-hidden="true"><circle cx="6" cy="6" r="5" fill="none" stroke="var(--accent)" stroke-width="1.1"/><ellipse cx="6" cy="6" rx="2.2" ry="5" fill="none" stroke="var(--accent)" stroke-width="1"/><path d="M1 6h10" stroke="var(--accent)" stroke-width="1"/></svg>
        <span>www.zelquin.com</span>
      </div>
    </div>
    <div class="card__band"></div>
  </section>
</main>
</body>
</html>
```